Animal Eye Clinic needs a Business card

We are a new veterinary ophthalmology practice (Ridgeline Pet Vision Care) and we need a business card designed. We only see animal eyes - we are not a regular veterinary clinic. We already have a logo. We are looking for a professional, good looking business card to hand out to our clients. We are looking for something simple but professional and contemporary. Our logo is likely the only picture/graphic that needs to be on the card.
Updates

Contact Information for Business Card

Delia Vossman, BSc, DVM, MSc, DipACVO
Veterinary Ophthalmologist

Phone: 250.418.3927
Email: ridgelinepetvisioncare@mailbox-example.net
Website: ridgelinepetvisioncare-example.net
Address: 1874 Thornbury Rd
Kelowna, BC, V1X 4M9

Colors

Designer to choose colors to be used in the design.

Requirements
Must have
• Our logo (attached)

```html
<!DOCTYPE html>
<html lang="en">
<head>
<meta charset="utf-8">
<title>Ridgeline Pet Vision Care – Business Card</title>
<link href="https://fonts.googleapis.com/css2?family=Roboto:wght@400;500;700&display=swap" rel="stylesheet">
<style>
  :root {
    --backdrop: #2a2a2a;
    --card: #232323;
    --card-front: #1b1b1b;
    --teal: #0aa0b4;
    --ink: #f2f2f2;
    --muted: #5a5a5a;
    --divider: #cfcfcf;
  }
  * { margin: 0; padding: 0; box-sizing: border-box; }
  html, body {
    width: 1200px; height: 901px; overflow: hidden;
    background: var(--backdrop);
    font-family: "Roboto", sans-serif;
  }
  .canvas { position: relative; width: 1200px; height: 901px; }
  .card {
    position: absolute; left: 250px; width: 700px; height: 400px;
    overflow: hidden;
  }
  .card--front { top: 35px; background: var(--card-front); }
  .card--back { top: 466px; background: var(--card); }

  .pattern-field {
    position: absolute; inset: 0;
    background: linear-gradient(115deg, #161616 0%, #1c1c1c 45%, #3a3a3a 75%, #4a4a4a 100%);
  }
  .brand {
    position: absolute; display: flex; align-items: center; gap: 14px;
  }
  .brand__mark {
    width: 44px; height: 44px; border-radius: 50%;
    background: var(--teal); flex: none;
  }
  .brand__name {
    color: var(--teal); font-weight: 700; font-size: 26px;
    line-height: 1.05; text-transform: uppercase; letter-spacing: 0.5px;
  }
  .card--front .brand { left: 380px; top: 250px; background: var(--card-front); padding: 10px 14px; }
  .card--back .brand { left: 40px; top: 175px; }
  .card--back .brand__name { font-size: 22px; }
  .card--back .brand__mark { width: 40px; height: 40px; }

  .decor-mark {
    position: absolute; right: -60px; top: 40px; width: 440px; height: 440px;
    border-radius: 50%;
    background: radial-gradient(circle at 50% 50%, #2f2f2f 0%, #292929 60%, rgba(35,35,35,0) 72%);
  }
  .divider {
    position: absolute; left: 300px; top: 160px; width: 1px; height: 170px;
    background: var(--divider);
  }
  .contact {
    position: absolute; left: 320px; top: 160px; color: var(--ink);
    font-size: 17px; line-height: 1.3;
  }
  .contact__name { color: var(--teal); font-weight: 700; font-size: 18px; }
  .contact__cred { font-size: 12px; font-weight: 500; }
  .contact__title { margin-bottom: 10px; }
  .contact__address { margin-bottom: 10px; }
  .contact__row { display: flex; align-items: center; gap: 8px; font-size: 15px; }
  .contact__row svg { width: 13px; height: 13px; flex: none; fill: var(--teal); }
  .accent { color: var(--teal); }
  .stripe {
    position: absolute; left: 0; right: 0; bottom: 0; height: 12px;
    background: var(--teal);
  }
</style>
</head>
<body>
<div class="canvas">

  <section class="card card--front">
    <div class="pattern-field" role="img" aria-label="Repeating tone-on-tone pattern of the clinic's eye emblem"></div>
    <div class="brand">
      <span class="brand__mark"></span>
      <span class="brand__name">Ridgeline<br>Pet Vision Care</span>
    </div>
  </section>

  <section class="card card--back">
    <div class="decor-mark" role="img" aria-label="Large faint clinic emblem in the background"></div>
    <div class="brand">
      <span class="brand__mark"></span>
      <span class="brand__name">Ridgeline<br>Pet Vision Care</span>
    </div>
    <div class="divider"></div>
    <div class="contact">
      <p><span class="contact__name">Delia Vossman</span><span class="contact__cred accent">, BSc, DVM, MSc, DipACVO</span></p>
      <p class="contact__title">Veterinary Ophthalmologist</p>
      <p class="contact__address">1874 Thornbury Rd<br>Kelowna, BC, V1X 4M9</p>
      <p class="contact__row">
        <svg viewBox="0 0 24 24"><path d="M6.6 10.8a15 15 0 0 0 6.6 6.6l2.2-2.2a1 1 0 0 1 1-.25 11.4 11.4 0 0 0 3.6.57 1 1 0 0 1 1 1V20a1 1 0 0 1-1 1A17 17 0 0 1 3 4a1 1 0 0 1 1-1h3.5a1 1 0 0 1 1 1c0 1.25.2 2.45.57 3.57a1 1 0 0 1-.25 1z"/></svg>
        250.418.3927
      </p>
      <p class="contact__row">
        <svg viewBox="0 0 24 24"><path d="M2 5h20v14H2z M3 6l9 7 9-7" fill="none" stroke="#0aa0b4" stroke-width="2"/></svg>
        ridgelinepetvisioncare@mailbox-example.net
      </p>
      <p class="contact__row">
        <svg viewBox="0 0 24 24"><circle cx="12" cy="12" r="10" fill="none" stroke="#0aa0b4" stroke-width="2"/><path d="M2 12h20M12 2c3 3 3 17 0 20M12 2c-3 3-3 17 0 20" fill="none" stroke="#0aa0b4" stroke-width="1.5"/></svg>
        <span>www.<span class="accent">ridgelinepetvisioncare-example</span>.net</span>
      </p>
    </div>
    <div class="stripe"></div>
  </section>

</div>
</body>
</html>
```